Satchel & Sundial needs new business card design

I need a new business card design. I'm looking for out-of-the-box design which represents the freedom of being a location independent entrepreneur.
I offer coaching, retreats and trips.
I would like to see designs with and without the photo.
Colors I use are black (#000000), green (#25A796) and brown (#D7C38C)
Website satchelandsundial.example

Target Market(s)

location independent entrepreneurs, digital nomads, people looking to swap the 9 to 5 for a lifestyle business

Industry/Entity Type

Business

Contact Information for Business Card

Dorota Falkner
Your Lifestyle Business Coach, Retreat & Trip Leader
http://satchelandsundial.example
hello@satchelandsundial.example
Live a life you don't need a holiday from

Font styles to use
Serif
Sans Serif

Requirements
Must have
• One side should contain only the logo. I would also consider having the "Live a life you don't need a holiday from" on that side too (depending on how it looks)
• Please show both sides on the designs.

```html
<!DOCTYPE html>
<html lang="en">
<head>
<meta charset="utf-8">
<title>Satchel &amp; Sundial – Business Card</title>
<link rel="stylesheet" href="https://fonts.googleapis.com/css2?family=Montserrat:wght@400;600;700&family=Libre+Baskerville&display=swap">
<style>
  :root {
    --ink: #000000;
    --teal: #25A796;
    --paper: #ffffff;
    --backdrop: #2b2b2b;
    --rule: #9a9a9a;
    --text: #1f1f1f;
  }
  * { box-sizing: border-box; margin: 0; padding: 0; }
  html, body { width: 1200px; height: 900px; overflow: hidden; }
  body {
    background: var(--backdrop);
    font-family: "Montserrat", Arial, sans-serif;
    color: var(--text);
    position: relative;
  }
  .card {
    position: absolute;
    left: 250px;
    width: 700px;
    height: 400px;
    background: var(--paper);
    border-radius: 26px;
    overflow: hidden;
  }
  .card--front { top: 40px; }
  .card--back { top: 470px; }

  .brand-name {
    font-family: "Montserrat", Arial, sans-serif;
    font-weight: 700;
    color: var(--ink);
    text-transform: uppercase;
    letter-spacing: 2px;
    white-space: nowrap;
  }

  /* front */
  .card--front .brand-name {
    position: absolute;
    top: 150px;
    left: 0; right: 0;
    text-align: center;
    font-size: 44px;
  }
  .card--front .brand-url {
    position: absolute;
    top: 218px;
    left: 0; right: 0;
    text-align: center;
    font-size: 16px;
    color: var(--ink);
  }
  .card--front .web-line {
    position: absolute;
    bottom: 42px;
    left: 0; right: 0;
    text-align: center;
    font-size: 19px;
    letter-spacing: 0.5px;
    color: var(--ink);
  }
  .accent { color: var(--teal); font-weight: 700; }

  /* back */
  .card--back .brand-name {
    position: absolute;
    top: 150px;
    left: 36px;
    width: 300px;
    font-size: 27px;
    line-height: 1.2;
    text-align: center;
    white-space: normal;
  }
  .divider {
    position: absolute;
    left: 352px;
    top: 70px;
    width: 1px;
    height: 180px;
    background: var(--rule);
  }
  .contact {
    position: absolute;
    left: 378px;
    top: 68px;
  }
  .contact__name {
    font-family: "Libre Baskerville", Georgia, serif;
    color: var(--teal);
    font-size: 25px;
    margin-bottom: 6px;
  }
  .contact__role {
    font-size: 14px;
    line-height: 1.35;
    color: var(--text);
    margin-bottom: 14px;
  }
  .contact__list { list-style: none; }
  .contact__list li {
    display: flex;
    align-items: center;
    gap: 10px;
    font-size: 14px;
    line-height: 1.6;
  }
  .contact__list svg { width: 11px; height: 11px; flex: none; }

  .tag-band {
    position: absolute;
    left: 0; right: 0;
    top: 300px;
    height: 26px;
    background: var(--teal);
  }
  .tagline {
    position: absolute;
    top: 296px;
    left: 250px;
    width: 400px;
    height: 34px;
    background: var(--ink);
    color: var(--paper);
    font-size: 15px;
    letter-spacing: 0.5px;
    text-transform: uppercase;
    display: flex;
    align-items: center;
    justify-content: center;
    white-space: nowrap;
  }
</style>
</head>
<body>

<section class="card card--front" aria-label="Card front">
  <p class="brand-name">Satchel &amp; Sundial</p>
  <p class="web-line">www.<span class="accent">satchelandsundial</span>.example</p>
</section>

<section class="card card--back" aria-label="Card back">
  <p class="brand-name">Satchel &amp; Sundial</p>
  <div class="divider"></div>
  <div class="contact">
    <h1 class="contact__name">Dorota Falkner</h1>
    <p class="contact__role">Your Lifestyle Business Coach<br>Retreat &amp; Trip Leader</p>
    <ul class="contact__list">
      <li>
        <svg viewBox="0 0 12 12" aria-hidden="true"><path d="M2.5 1 L4.5 1 L5.3 3.6 L4 4.6 Q5 7 7.4 8 L8.4 6.7 L11 7.5 L11 9.5 Q10 11 8.5 11 Q2 9.5 1 3.5 Q1 2 2.5 1 Z" fill="var(--teal)"/></svg>
        <span>+330 5550-0142</span>
      </li>
      <li>
        <svg viewBox="0 0 12 12" aria-hidden="true"><rect x="1" y="2.5" width="10" height="7" fill="none" stroke="var(--teal)" stroke-width="1.4"/><path d="M1 2.5 L6 6.5 L11 2.5" fill="none" stroke="var(--teal)" stroke-width="1.4"/></svg>
        <span>hello@satchelandsundial.example</span>
      </li>
      <li>
        <svg viewBox="0 0 12 12" aria-hidden="true"><circle cx="6" cy="6" r="5" fill="none" stroke="var(--teal)" stroke-width="1.3"/><ellipse cx="6" cy="6" rx="2.2" ry="5" fill="none" stroke="var(--teal)" stroke-width="1"/><path d="M1 6 H11" stroke="var(--teal)" stroke-width="1"/></svg>
        <span>www.<span class="accent">satchelandsundial</span>.example</span>
      </li>
    </ul>
  </div>
  <div class="tag-band"></div>
  <p class="tagline">Live a life you don't need a holiday from</p>
</section>

</body>
</html>
```